Billboard design for dentist that sees only children

I own a 12' x 25' digital billboard and I need help with billboard design. My wife is a general dentist that only sees children and is very passionate about giving them a quality dental experience . She has a great reputation in town. Obviously with a billboard there can't be a lot of reading. Maybe something that shows safety, love, experience and children. I am completely open to your ideas. In addition I have other businesses that also need billboard design so this could lead to more work. If you go to Maplecovedental.com under the about section you will find more information about the practice and our phone number. Attached is our logo which could be changed and content specs for the digital billboard. Happy Designing!!

Target Market(s)

Parents with children

Colors

Designer to choose colors to be used in the design.

Requirements
Must have
• Must attract attention and be nice to look at.
Nice to have
• Probably should have children in the picture ..... Maybe
Should not have
• If I see something I don't like I will let you know

```html
<!DOCTYPE html>
<html lang="en">
<head>
<meta charset="utf-8">
<title>Maple Cove Dental – Billboard</title>
<link rel="stylesheet" href="https://fonts.googleapis.com/css2?family=Nunito+Sans:wght@400;600;700;800&display=swap">
<style>
  :root {
    --page-bg: #e4e4e4;
    --board-bg: #f7f9fb;
    --headline-blue: #2f5d9e;
    --headline-navy: #1c3e6e;
    --phone-teal: #1e5b56;
    --brand-teal: #2a7d8c;
    --tagline-blue: #2f6fb0;
    --address-ink: #2b3a48;
    --clinic-light: #dfeaf2;
    --clinic-mid: #a9cbe2;
    --glove-blue: #5d9bd6;
    --bib-blue: #1f62b0;
    --chair-navy: #123d74;
    --warm-tone: #e6c3a3;
    --hair-tone: #b87a4f;
  }
  * { margin: 0; padding: 0; box-sizing: border-box; }
  html, body {
    width: 1200px;
    height: 752px;
    overflow: hidden;
    background: var(--page-bg);
    font-family: "Nunito Sans", Arial, sans-serif;
  }
  .billboard {
    position: absolute;
    left: 30px;
    top: 102px;
    width: 1140px;
    height: 548px;
    background: var(--board-bg);
    overflow: hidden;
  }
  .photo-area {
    position: absolute;
    right: 0;
    top: 0;
    width: 700px;
    height: 100%;
    background:
      linear-gradient(90deg, var(--board-bg) 0%, rgba(247,249,251,0.85) 14%, rgba(247,249,251,0) 36%),
      radial-gradient(ellipse 150px 130px at 76% 24%, var(--hair-tone) 0%, rgba(184,122,79,0) 100%),
      radial-gradient(ellipse 170px 160px at 72% 44%, var(--warm-tone) 0%, rgba(230,195,163,0) 100%),
      radial-gradient(ellipse 120px 90px at 40% 66%, var(--glove-blue) 0%, rgba(93,155,214,0) 100%),
      linear-gradient(165deg, var(--clinic-light) 0%, var(--clinic-mid) 42%, var(--glove-blue) 60%, var(--bib-blue) 76%, var(--chair-navy) 100%);
  }
  .headline {
    position: absolute;
    left: 70px;
    top: 56px;
    line-height: 1.05;
    z-index: 1;
  }
  .headline-lead {
    display: block;
    font-size: 47px;
    font-weight: 700;
    color: var(--headline-blue);
  }
  .headline-main {
    display: block;
    margin-left: 36px;
    margin-top: 4px;
    font-size: 52px;
    font-weight: 800;
    color: var(--headline-navy);
  }
  .phone {
    position: absolute;
    left: 86px;
    top: 246px;
    display: flex;
    align-items: center;
    gap: 18px;
    color: var(--phone-teal);
    z-index: 1;
  }
  .phone-icon { width: 44px; height: 44px; }
  .phone-number {
    font-size: 64px;
    font-weight: 600;
    letter-spacing: 1px;
  }
  .brand {
    position: absolute;
    left: 50px;
    top: 418px;
    display: flex;
    align-items: center;
    gap: 14px;
    z-index: 1;
  }
  .brand-mark {
    width: 40px;
    height: 40px;
    border-radius: 50%;
    background: var(--brand-teal);
  }
  .brand-name {
    font-size: 38px;
    font-weight: 600;
    color: var(--brand-teal);
    line-height: 1;
  }
  .brand-tagline {
    display: block;
    margin-top: 4px;
    margin-left: 100px;
    font-size: 17px;
    font-weight: 600;
    color: var(--tagline-blue);
  }
  .address {
    position: absolute;
    left: 52px;
    top: 506px;
    font-size: 16px;
    font-weight: 400;
    color: var(--address-ink);
    letter-spacing: 0.3px;
    z-index: 1;
  }
</style>
</head>
<body>
  <main class="billboard">
    <div class="photo-area" role="img" aria-label="Photo of a smiling boy in a blue bib sitting in a dental chair while a gloved dentist holds a dental mirror, bright clinic behind"></div>

    <h1 class="headline">
      <span class="headline-lead">We Love Kids and Know</span>
      <span class="headline-main">HOW TO CARE FOR THEM</span>
    </h1>

    <div class="phone">
      <svg class="phone-icon" viewBox="0 0 44 44" aria-hidden="true">
        <circle cx="22" cy="22" r="19" fill="none" stroke="currentColor" stroke-width="3"/>
        <path d="M15 12c1.5-1 3-0.8 3.8 0.6l2 3.6c0.6 1.1 0.3 2.3-0.7 3l-1.4 1c1.2 2.6 3.2 4.6 5.8 5.8l1-1.4c0.7-1 1.9-1.3 3-0.7l3.6 2c1.4 0.8 1.6 2.3 0.6 3.8-1.4 2-3.6 2.8-6 2-6.6-2.2-11.4-7-13.6-13.6-0.8-2.4 0-4.6 2-6z" fill="currentColor"/>
      </svg>
      <span class="phone-number">123-456-7890</span>
    </div>

    <div class="brand">
      <span class="brand-mark" aria-hidden="true"></span>
      <div>
        <span class="brand-name">Maple Cove Dental</span>
        <span class="brand-tagline">general dentistry for children</span>
      </div>
    </div>

    <p class="address">123 STREET NUMBER AND STREET HERE</p>
  </main>
</body>
</html>
```